Alberta, Canada based Environmental Oilfield Consultant need a Business Card Design

We need a business card design for a year old company based in Edmonton, Alberta, Canada called Cindermoor Consulting Inc. We are environmental consultants primarily for oilfield based companies (pipeline cleanup, site consultations, environmental site training, and site evaluations).

We like the color blue or green, something very clean and crisp looking.
We don't really care if there is an otter on it but most of our work is land based and nothing really to do with oceans or larger bodies of water.

The name Cindermoor was the name of our fathers boat, and named our company that in his memory.

```html
<!DOCTYPE html>
<html lang="en">
<head>
<meta charset="utf-8">
<title>Cindermoor Consulting Inc. – Business Card</title>
<link rel="stylesheet" href="https://fonts.googleapis.com/css2?family=Exo+2:wght@400;600;900&display=swap">
<style>
  :root {
    --bg: #e6ebe8;
    --card: #ffffff;
    --card-shade: #f1f3f4;
    --green: #2e9e5b;
    --green-deep: #1f7a45;
    --green-light: #c9ecd4;
    --blue: #1f6fa8;
    --blue-deep: #17558a;
    --ink: #3f4a52;
    --ink-soft: #5d6870;
  }
  * { box-sizing: border-box; margin: 0; padding: 0; }
  html, body { width: 1071px; height: 1200px; overflow: hidden; }
  body {
    background: var(--bg);
    font-family: "Exo 2", sans-serif;
    color: var(--ink);
    position: relative;
  }
  .card {
    position: absolute;
    left: 85px;
    width: 900px;
    height: 514px;
    background: linear-gradient(135deg, var(--card) 40%, var(--card-shade));
    box-shadow: 0 10px 30px rgba(30, 50, 45, 0.22);
    overflow: hidden;
  }
  .card--front { top: 50px; }
  .card--back { top: 636px; }

  /* front */
  .holder { position: absolute; left: 0; top: 110px; padding-left: 44px; }
  .holder__marker {
    position: absolute; left: 0; top: 6px;
    width: 26px; height: 26px; background: var(--green);
  }
  .holder__name {
    font-size: 30px; font-weight: 400; color: var(--green);
    letter-spacing: 0.5px; text-transform: uppercase; line-height: 1.2;
  }
  .holder__role {
    font-size: 19px; font-weight: 600; color: var(--ink);
    text-transform: uppercase; letter-spacing: 0.5px; margin-top: 2px;
  }
  .contacts {
    position: absolute; left: 44px; top: 250px;
    list-style: none; font-size: 16px; color: var(--ink-soft);
  }
  .contacts li { display: flex; align-items: center; gap: 12px; height: 32px; }
  .contacts svg { width: 16px; height: 16px; flex: none; }

  .wordmark {
    position: absolute; right: 70px; top: 56px;
    font-weight: 900; font-size: 66px; line-height: 0.95;
    color: var(--blue); text-align: left; white-space: nowrap;
  }
  .accent-band {
    position: absolute; left: 390px; right: 0; top: 246px; height: 84px;
    background: linear-gradient(90deg, var(--green-light) 0%, var(--green) 45%, var(--blue) 100%);
  }
  .address {
    position: absolute; left: 420px; top: 352px;
    font-size: 22px; font-weight: 600; color: var(--ink); line-height: 1.35;
  }
  .edge-strip {
    position: absolute; left: 390px; right: 0; bottom: 0; height: 34px;
    background: linear-gradient(90deg, var(--green-deep), var(--blue-deep));
  }

  /* back */
  .card--back .wordmark {
    right: auto; top: 50%; left: 50%;
    transform: translate(-50%, -50%);
    font-size: 84px;
  }
  .card--back .edge-strip { left: 0; height: 12px; }
</style>
</head>
<body>
  <section class="card card--front" aria-label="Business card front">
    <div class="holder">
      <span class="holder__marker"></span>
      <p class="holder__name">Dana Whitfield</p>
      <p class="holder__role">General Manager</p>
    </div>
    <ul class="contacts">
      <li><svg viewBox="0 0 16 16"><path d="M4 1l3 3-2 2c1 2 3 4 5 5l2-2 3 3-2 3C7 15 1 9 1 3z" fill="var(--green)"/></svg>012 555 0147</li>
      <li><svg viewBox="0 0 16 16"><rect x="2" y="2" width="12" height="12" fill="none" stroke="var(--green)" stroke-width="2"/></svg>012 555 0147</li>
      <li><svg viewBox="0 0 16 16"><rect x="1" y="3" width="14" height="10" fill="var(--green)"/></svg>hello@cindermoor.ca</li>
      <li><svg viewBox="0 0 16 16"><circle cx="8" cy="8" r="7" fill="var(--green)"/></svg>www.cindermoor.ca</li>
    </ul>
    <div class="wordmark">Cindermoor<br>Consulting</div>
    <div class="accent-band"></div>
    <p class="address">2140 Ridgeline Road,<br>3rd Floor, Suite W.</p>
    <div class="edge-strip"></div>
  </section>

  <section class="card card--back" aria-label="Business card back">
    <div class="wordmark">Cindermoor<br>Consulting</div>
    <div class="edge-strip"></div>
  </section>
</body>
</html>
```